food delivery web site design

Currently we have a smartphone app (ios/android) that is being used by our clients to make orders to about 30 different restaurants.

We would like to extent this and have also a website that is able to mimic the same functionalities:
- register
- show restaurants based on the selected address
- make order to an restaurant
- being able to process orders for other registered users (please read the attached doc for complete info on this)

Take a look at the attached doc for more info.

```html
<!DOCTYPE html>
<html lang="ro">
<head>
<meta charset="utf-8">
<title>Cookly – Adaugă/Editează adresa</title>
<link href="https://fonts.googleapis.com/css2?family=Bebas+Neue&family=Open+Sans:wght@400;600&display=swap" rel="stylesheet">
<style>
  :root {
    --red: #9e170c;
    --red-dark: #7d1008;
    --brown: #2b2220;
    --yellow: #f5c64a;
    --grey-text: #666666;
    --grey-light: #c9c9c9;
    --grey-line: #d4d4d4;
    --grey-btn: #666666;
    --footer-bg: #262423;
    --white: #ffffff;
  }
  * { box-sizing: border-box; margin: 0; padding: 0; }
  html, body { width: 1200px; height: 1200px; overflow: hidden; background: var(--white); }
  body { position: relative; font-family: "Open Sans", Arial, sans-serif; color: var(--grey-text); }
  .display { font-family: "Bebas Neue", "Oswald", sans-serif; font-weight: 400; }
  .abs { position: absolute; }

  /* header */
  .header-pattern { left: 0; top: 0; width: 1200px; height: 52px; background: linear-gradient(#fafafa, #eeeeee); }
  .header-band { left: 0; top: 52px; width: 1200px; height: 51px; background: var(--red); border-bottom: 2px solid var(--red-dark); }
  .header-rule { left: 0; top: 104px; width: 1200px; height: 1px; background: var(--red); }
  .band-line { top: 78px; height: 1px; background: rgba(255,255,255,.6); }
  .band-dots { top: 77px; left: 609px; width: 277px; border-top: 2px dotted rgba(255,255,255,.45); }
  .call { left: 350px; top: 62px; font-size: 29px; color: var(--white); display: flex; align-items: center; gap: 6px; white-space: nowrap; }
  .call .phone-number { color: var(--yellow); }
  .nav-link { top: 67px; font-size: 19px; color: var(--white); display: flex; align-items: center; gap: 6px; text-decoration: none; }
  .brand-badge { left: 138px; top: 0; width: 159px; height: 158px; }
  .brand-circle { left: 163px; top: 23px; width: 110px; height: 110px; border-radius: 50%; background: var(--white); display: flex; align-items: center; justify-content: center; }
  .brand-name { font-family: "Open Sans", sans-serif; font-weight: 600; font-size: 22px; color: var(--red); }

  /* page title */
  .page-title { left: 140px; top: 232px; font-size: 58px; color: var(--grey-light); letter-spacing: .5px; }
  .title-rule { left: 138px; top: 296px; width: 924px; height: 1px; background: var(--grey-line); }

  /* form */
  .field-label { font-size: 22px; color: var(--grey-text); line-height: 1; }
  .field { border: 1px solid var(--grey-line); background: var(--white); }
  .field-city { font-family: "Bebas Neue", sans-serif; font-size: 18px; color: var(--grey-light); padding: 9px 0 0 8px; }

  .btn { top: 904px; height: 41px; color: var(--white); font-size: 22px; display: flex; align-items: center; justify-content: center; }
  .btn-save { left: 138px; width: 165px; background: var(--red); }
  .btn-cancel { left: 321px; width: 107px; background: var(--grey-btn); }

  /* saved addresses */
  .saved-title { left: 665px; top: 338px; font-size: 23px; color: var(--grey-text); }
  .saved-rule { left: 665px; top: 365px; width: 313px; height: 1px; background: var(--grey-line); }
  .address-text { left: 665px; width: 310px; font-size: 13px; line-height: 17px; color: var(--grey-text); }
  .address-text b { font-weight: 600; }
  .address-actions { left: 664px; font-size: 17px; display: flex; gap: 17px; }
  .action-edit { color: #333333; }
  .action-delete { color: var(--red); }
  .address-divider { left: 665px; width: 312px; border-top: 1px dotted #bbbbbb; }

  /* footer */
  .footer { left: 0; top: 1145px; width: 1200px; height: 55px; background: var(--footer-bg); }
  .footer-nav { left: 138px; top: 1163px; font-size: 13px; color: var(--white); display: flex; gap: 9px; }
  .footer-nav .sep { color: #555; }
  .copyright { right: 138px; top: 1163px; font-size: 13px; color: var(--white); }
</style>
</head>
<body>

<header>
  <div class="abs header-pattern" role="img" aria-label="Food doodle pattern band"></div>
  <div class="abs header-band"></div>
  <div class="abs header-rule"></div>
  <div class="abs band-line" style="left:297px;width:35px"></div>
  <div class="abs band-dots"></div>
  <div class="abs band-line" style="left:1063px;width:137px"></div>

  <div class="abs call display">
    <span>SUNĂ-NE LA</span>
    <svg width="16" height="20" viewBox="0 0 16 20" aria-hidden="true"><path d="M4 1 L7 5 L5 7 C6 10 8 13 10 14 L12 12 L15 15 L13 18 C7 18 1 10 2 3 Z" fill="#f5c64a"/></svg>
    <span class="phone-number">0700 123 456</span>
  </div>

  <a class="abs nav-link display" style="left:906px">
    <svg width="15" height="14" viewBox="0 0 15 14" aria-hidden="true"><path d="M1 13 C1 7 4 5 9 5 V1 L14 6 L9 11 V8 C5 8 3 9 1 13 Z" fill="#fff"/></svg>
    LOGIN
  </a>
  <a class="abs nav-link display" style="left:980px">
    <svg width="16" height="14" viewBox="0 0 16 14" aria-hidden="true"><circle cx="6" cy="4" r="3.2" fill="#fff"/><path d="M0 13 C0 9 3 8 6 8 C9 8 12 9 12 13 Z" fill="#fff"/><path d="M13 1 V6 M10.5 3.5 H15.5" stroke="#fff" stroke-width="1.6"/></svg>
    SIGN IN
  </a>

  <svg class="abs brand-badge" viewBox="0 0 159 158" aria-hidden="true">
    <path d="M0 0 H159 V128 L135 152 H24 L0 128 Z" fill="#2b2220"/>
    <path d="M6 0 V125 L27 146 H132 L153 125 V0" fill="none" stroke="#5a4a45" stroke-width="1"/>
  </svg>
  <div class="abs brand-circle"><span class="brand-name">Cookly</span></div>
</header>

<main>
  <h1 class="abs page-title display">ADAUGĂ/EDITEAZĂ ADRESA</h1>
  <div class="abs title-rule"></div>

  <form class="address-form">
    <label class="abs field-label display" style="left:138px;top:338px">ORAȘ</label>
    <div class="abs field field-city" style="left:138px;top:366px;width:102px;height:37px">BUCUREȘTI</div>

    <label class="abs field-label display" style="left:138px;top:430px">STRADĂ</label>
    <div class="abs field" style="left:138px;top:458px;width:221px;height:37px"></div>
    <label class="abs field-label display" style="left:376px;top:430px">NR.</label>
    <div class="abs field" style="left:377px;top:458px;width:55px;height:37px"></div>

    <label class="abs field-label display" style="left:138px;top:522px">BLOC</label>
    <div class="abs field" style="left:138px;top:550px;width:102px;height:37px"></div>
    <label class="abs field-label display" style="left:258px;top:522px">SCARĂ</label>
    <div class="abs field" style="left:258px;top:550px;width:101px;height:37px"></div>
    <label class="abs field-label display" style="left:376px;top:522px">NR. APT.</label>
    <div class="abs field" style="left:377px;top:550px;width:55px;height:37px"></div>

    <label class="abs field-label display" style="left:138px;top:614px">ALTE INFORMAȚII</label>
    <div class="abs field" style="left:138px;top:642px;width:305px;height:93px"></div>

    <label class="abs field-label display" style="left:138px;top:762px">NUME ADRESĂ</label>
    <div class="abs field" style="left:138px;top:790px;width:176px;height:37px"></div>

    <div class="abs btn btn-save display">SALVEAZĂ ADRESA</div>
    <div class="abs btn btn-cancel display">ANULEAZĂ</div>
  </form>

  <section class="saved-addresses">
    <h2 class="abs saved-title display">3 ADRESE SALVATE</h2>
    <div class="abs saved-rule"></div>

    <p class="abs address-text" style="top:381px"><b>1.</b> Lorem ipsum dolor sit amet, consectetur adipiscing elit</p>
    <div class="abs address-actions display" style="top:427px"><span class="action-edit">EDITEAZĂ</span><span class="action-delete">ȘTERGE</span></div>
    <div class="abs address-divider" style="top:459px"></div>

    <p class="abs address-text" style="top:473px"><b>2.</b> Illum mallem levares, quo optimum atque humanissimum virum</p>
    <div class="abs address-actions display" style="top:519px"><span class="action-edit">EDITEAZĂ</span><span class="action-delete">ȘTERGE</span></div>
    <div class="abs address-divider" style="top:551px"></div>

    <p class="abs address-text" style="top:565px"><b>3.</b> Ab hoc autem quaedam non melius quam veteres, quaedam omnino relicta</p>
    <div class="abs address-actions display" style="top:611px"><span class="action-edit">EDITEAZĂ</span><span class="action-delete">ȘTERGE</span></div>
  </section>
</main>

<footer>
  <div class="abs footer" role="img" aria-label="Dark footer band with food doodle pattern"></div>
  <nav class="abs footer-nav">
    <span>Contactează-ne</span><span class="sep">|</span>
    <span>Despre noi</span><span class="sep">|</span>
    <span>Partenerii noștri</span><span class="sep">|</span>
    <span>FAQ</span><span class="sep">|</span>
    <span>Devino partener</span>
  </nav>
  <p class="abs copyright">Copyright © 2013 Cookly.ro. Toate drepturile rezervate.</p>
</footer>

</body>
</html>
```